TALMORK

The business want a professional looking business card. We have a scetch we will add but want the extra upgrade, and would like more suggestions for variations of our business cards.

```html
<!DOCTYPE html>
<html lang="en">
<head>
<meta charset="utf-8">
<title>TALMORK – Business Card</title>
<link href="https://fonts.googleapis.com/css2?family=Playfair+Display:wght@400;700&family=Poppins:wght@400&display=swap" rel="stylesheet">
<style>
  :root {
    --backdrop: #3a3a3c;
    --card: #1f1f20;
    --gold: #d8b04a;
    --ink-light: #ececec;
    --emboss: #2b2b2d;
    --emboss-hi: #3a3a3d;
  }
  * { margin: 0; padding: 0; box-sizing: border-box; }
  html, body { width: 1200px; height: 900px; overflow: hidden; }
  body {
    background: var(--backdrop);
    position: relative;
    font-family: "Poppins", sans-serif;
  }
  .card {
    position: absolute;
    width: 600px;
    height: 343px;
    background: var(--card);
    border-radius: 22px;
    box-shadow: 0 14px 30px rgba(0,0,0,0.45);
    overflow: hidden;
  }
  .card--back { left: 520px; top: 70px; }
  .card--front { left: 120px; top: 470px; }

  /* Back side */
  .back-mark {
    position: absolute;
    left: 0; right: 0; top: 70px;
    display: flex; flex-direction: column; align-items: center; gap: 26px;
  }
  .back-mark__dot {
    width: 64px; height: 64px; border-radius: 50%;
    background: var(--emboss);
    box-shadow: inset 2px 2px 4px rgba(0,0,0,0.6), inset -1px -1px 2px var(--emboss-hi);
  }
  .back-mark__name {
    font-family: "Playfair Display", serif;
    font-weight: 400;
    font-size: 58px;
    letter-spacing: 16px;
    color: var(--emboss);
    text-shadow: 1px 1px 0 #111;
  }

  /* Front side */
  .front-info {
    position: absolute; left: 0; top: 0; width: 360px; height: 100%;
    z-index: 2;
  }
  .brand {
    position: absolute; left: 40px; width: 300px; top: 30px;
    display: flex; flex-direction: column; align-items: center; gap: 12px;
  }
  .brand__dot { width: 30px; height: 30px; border-radius: 50%; background: var(--gold); }
  .brand__name {
    font-family: "Playfair Display", serif;
    font-size: 30px;
    letter-spacing: 9px;
    color: var(--gold);
    white-space: nowrap;
  }
  .holder { position: absolute; left: 80px; top: 140px; }
  .holder__name {
    font-family: "Playfair Display", serif;
    font-weight: 700;
    font-size: 25px;
    color: var(--gold);
    line-height: 1.1;
    white-space: nowrap;
  }
  .holder__role, .holder__alt {
    font-size: 15px; color: var(--ink-light); line-height: 1.4;
  }
  .contact {
    position: absolute; left: 50px; top: 236px;
    list-style: none;
    display: flex; flex-direction: column; gap: 6px;
  }
  .contact__item {
    display: flex; align-items: center; gap: 10px;
    font-size: 16px; color: var(--ink-light);
    white-space: nowrap;
  }
  .contact__icon { width: 14px; height: 14px; fill: var(--gold); flex: none; }
  .decor-disc {
    position: absolute; right: 30px; top: 60px;
    width: 210px; height: 210px; border-radius: 50%;
    background: radial-gradient(circle at 35% 35%, #3c3c3f, #141415 75%);
    z-index: 1;
  }
</style>
</head>
<body>
  <section class="card card--back" aria-label="Card back">
    <div class="back-mark">
      <div class="back-mark__dot"></div>
      <div class="back-mark__name">TALMORK</div>
    </div>
  </section>

  <section class="card card--front" aria-label="Card front">
    <div class="front-info">
      <div class="brand">
        <div class="brand__dot"></div>
        <div class="brand__name">TALMORK</div>
      </div>
      <div class="holder">
        <p class="holder__name">Talmork Haraldsen</p>
        <p class="holder__role">CEO &amp; Founder</p>
        <p class="holder__alt">Anders Lie Haugland</p>
      </div>
      <ul class="contact">
        <li class="contact__item">
          <svg class="contact__icon" viewBox="0 0 16 16"><path d="M3 1h3l1.5 4-2 1.2a9 9 0 0 0 4.3 4.3L11 8.5l4 1.5v3a2 2 0 0 1-2 2A13 13 0 0 1 1 3a2 2 0 0 1 2-2z"/></svg>
          004790018274
        </li>
        <li class="contact__item">
          <svg class="contact__icon" viewBox="0 0 16 16"><path d="M1 3h14v10H1z M1 3l7 6 7-6" stroke="#1f1f20" stroke-width="1.2"/></svg>
          talmork.llc@postmail.com
        </li>
        <li class="contact__item">
          <svg class="contact__icon" viewBox="0 0 16 16"><circle cx="8" cy="8" r="7"/><path d="M1 8h14M8 1c-3 3-3 11 0 14M8 1c3 3 3 11 0 14" stroke="#1f1f20" stroke-width="1" fill="none"/></svg>
          www.talmork.llc
        </li>
      </ul>
    </div>
    <div class="decor-disc" role="img" aria-label="Large embossed brand emblem in glossy black"></div>
  </section>
</body>
</html>
```